BRAMBLEFORD CONSTRUCTIONS B-Card

I currently have a b-card design but will be removing the image (tree) from the logo and have text only.
I want the card to be classy and strong within the building and construction industry.
I will be using Spot UV on the cards as per the attached examples. I will also send through some sketched ideas that I have in mind.
The color blue is similar to the image (No. 6) attached images

Target Market(s)

middle to maturre aged.
Home Owners / Renovators and Builders

Industry/Entity Type

Construction

Contact Information for Business Card

BRAMBLEFORD CONSTRUCTIONS
Name: Gareth Pennick
Title: Project Manager
Mobile: 0427 351 804
Office: (08) 9316 5172
Address: 47C Corvell Street, Malaga WA 6090
Email: info@bramblefordhomes.com.au
PO Box: 3817 Malaga WA 6944

Colors
0592cd
33a6d7
85cae6
1b1b1b

Requirements
Must have
• 1. It must have spot UV on the front of card, maybe back of card too
• 2. I really like the blue on image 6. (or at least a really cool electric blue against the charcoal grey background)
• 3. The font must be slimline and modern. Easy to read
• 4. There must be no black used on the card... Only greys and dark charcoal greys
• 5. Use only the text from the logo "Brambleford Constructions" Not the image of the tree. I am wanting the b-cards to be more masculine.
Nice to have
• 1. I like the design concept on image 6. but happy to see what else you can do with the Spot UV
• 2. Unless you have a really cool idea of the image of the tree (from previous logo) Spot UV somewhere in the design concept thats original and different then I am keen to see what you come up with
• 3. Try changing the color of the logo eg. full white or Blue and white
• 4. Another option is to have the Brambleford Logo on the front of card with the spot UV in the background of text which we specialise in eg, Roofing, Ceiling, Insulation, Gutter Guards, Electrical, Insurance etc and we can add or reduce items as required. Similar to image 12.
Should not have
• Do not include the image of the tree from previous logo. unless you have a really cool idea of Spot UV somewhere in the design concept thats original and different.

```html
<!DOCTYPE html>
<html lang="en">
<head>
<meta charset="UTF-8">
<title>Brambleford Constructions – Business Card</title>
<link rel="stylesheet" href="https://fonts.googleapis.com/css2?family=Montserrat:wght@400;700&family=Source+Sans+3:wght@400;600;700&display=swap">
<style>
  :root {
    --stage: #4a423d;
    --card: #1b1b1b;
    --card-edge: #242424;
    --blue: #33a6d7;
    --blue-deep: #0592cd;
    --blue-soft: #85cae6;
    --text-light: #d9d9d9;
    --text-bright: #f2f2f2;
    --uv: #272727;
  }
  * { margin: 0; padding: 0; box-sizing: border-box; }
  html, body {
    width: 1200px; height: 900px; overflow: hidden;
    background: var(--stage);
    font-family: "Source Sans 3", "Segoe UI", sans-serif;
  }
  .canvas { position: relative; width: 1200px; height: 900px; }

  .card {
    position: absolute;
    top: 307px;
    width: 500px; height: 286px;
    background: var(--card);
    border: 1px solid var(--card-edge);
    overflow: hidden;
    box-shadow: 0 10px 30px rgba(20, 15, 12, 0.45);
  }
  .card--front { left: 70px; }
  .card--back  { left: 630px; }

  .wordmark {
    position: absolute;
    color: var(--blue);
    font-family: "Montserrat", "Segoe UI", sans-serif;
    line-height: 1;
  }
  .wordmark__name { display: block; font-weight: 700; font-size: 36px; letter-spacing: -0.5px; }
  .wordmark__sub  { display: block; font-weight: 400; font-size: 13px; letter-spacing: 11.4px; margin-top: 5px; padding-left: 2px; }

  .card--front .wordmark { left: 60px; top: 66px; }

  .person { position: absolute; left: 60px; top: 146px; width: 180px; text-align: right; }
  .person__name  { color: var(--blue); font-weight: 700; font-size: 17px; line-height: 1.1; }
  .person__title { color: var(--text-light); font-size: 13px; line-height: 1.25; }

  .phones { position: absolute; left: 256px; top: 144px; list-style: none; }
  .phones li { display: flex; align-items: center; gap: 7px; color: var(--text-light); font-size: 13px; line-height: 19px; }
  .phones svg { width: 10px; height: 10px; fill: var(--blue); }

  .address { position: absolute; left: 60px; top: 206px; width: 306px; text-align: right;
             color: var(--text-light); font-size: 13px; line-height: 20px; }
  .address strong { font-weight: 700; color: var(--text-bright); }

  .uv-tree {
    position: absolute; left: 110px; top: -10px; width: 400px; height: 310px;
    background: radial-gradient(ellipse at 60% 40%, var(--uv) 0%, #212121 55%, var(--card) 80%);
  }
  .card--back .wordmark { left: 96px; top: 108px; }
</style>
</head>
<body>
<main class="canvas">

  <section class="card card--front" aria-label="Business card front">
    <div class="wordmark">
      <span class="wordmark__name">BRAMBLEFORD</span>
      <span class="wordmark__sub">CONSTRUCTIONS</span>
    </div>

    <div class="person">
      <p class="person__name">Gareth Pennick</p>
      <p class="person__title">Project Manager</p>
    </div>

    <ul class="phones">
      <li>
        <svg viewBox="0 0 10 10" aria-hidden="true"><rect x="2" y="0" width="6" height="10" rx="1.2"/><rect x="3" y="1.4" width="4" height="6" fill="#1b1b1b"/></svg>
        0427 351 804
      </li>
      <li>
        <svg viewBox="0 0 10 10" aria-hidden="true"><path d="M2 0.5 L3.8 0.5 L4.3 3 L3 3.8 C3.6 5.3 4.7 6.4 6.2 7 L7 5.7 L9.5 6.2 L9.5 8 C9.5 9 8.8 9.5 8 9.5 C4 9.2 0.8 6 0.5 2 C0.5 1.2 1 0.5 2 0.5 Z"/></svg>
        (08) 9316 5172
      </li>
    </ul>

    <p class="address">
      47C Corvell Street, Denholm WA 6071<br>
      <strong>PO Box:</strong> 3817 Denholm WA 6975
    </p>
  </section>

  <section class="card card--back" aria-label="Business card back">
    <div class="uv-tree" role="img" aria-label="Spot UV gloss tree illustration, dark on charcoal"></div>
    <div class="wordmark">
      <span class="wordmark__name">BRAMBLEFORD</span>
      <span class="wordmark__sub">CONSTRUCTIONS</span>
    </div>
  </section>

</main>
</body>
</html>
```